Dog grooming business card
This is a business card for m dog grooming business like it say above.
In the priorities box below I will have the text that I want on the card.

Industry/Entity Type

Business

Colors

Designer to choose colors to be used in the design.

Requirements
Must have
• My logo and the insurance stamp must be on the card.

Text it must have :

Professional grooming services
Email: lunabrisk@mailvale.net
Text or call 1 705 318 6052
TWF certified/member
Pet first aid certified
Next appointment ___________________________________
Nice to have
• Greens to match my logo

```html
<!DOCTYPE html>
<html lang="en">
<head>
<meta charset="utf-8">
<title>Luna Brisk – Business Card</title>
<link rel="stylesheet" href="https://fonts.googleapis.com/css2?family=Libre+Baskerville:wght@400;700&display=swap">
<style>
  :root {
    --bg: #e4e6ea;
    --card: #ffffff;
    --green: #95c83a;
    --green-soft: #86b533;
    --ink: #1d1d1b;
    --badge: #2f7fd0;
    --line: #3a3a3a;
  }
  * { box-sizing: border-box; margin: 0; padding: 0; }
  html, body { width: 1200px; height: 960px; overflow: hidden; }
  body {
    background: var(--bg);
    font-family: "Libre Baskerville", Georgia, serif;
    color: var(--ink);
    position: relative;
  }
  .card {
    position: absolute;
    left: 220px;
    width: 760px;
    height: 434px;
    background: var(--card);
    overflow: hidden;
    box-shadow: 0 6px 18px rgba(0,0,0,.18);
  }
  .card--front { top: 30px; }
  .card--back { top: 496px; }
  .card__panel {
    position: absolute;
    inset: 0;
    background: var(--green);
  }
  .card--front .card__panel { clip-path: polygon(0 0, 40% 0, 62% 100%, 0 100%); }
  .card--back .card__panel { clip-path: polygon(0 0, 42% 0, 58% 100%, 0 100%); }
  .decor-mark {
    position: absolute;
    left: 40px;
    top: 90px;
    width: 240px;
    height: 250px;
    border-radius: 50%;
    background: radial-gradient(circle, var(--green-soft) 0%, rgba(134,181,51,0) 70%);
  }
  .brand {
    position: absolute;
    display: flex;
    align-items: center;
    gap: 14px;
    font-weight: 700;
    color: var(--ink);
    white-space: nowrap;
  }
  .brand__dot {
    width: 18px; height: 18px; border-radius: 50%;
    background: var(--ink);
  }
  .card--front .brand { left: 420px; top: 186px; font-size: 36px; }
  .card--back .brand { left: 40px; top: 190px; font-size: 32px; }
  .badge {
    position: absolute;
    right: 34px;
    top: 26px;
    width: 86px;
    height: 36px;
    border: 2px solid var(--badge);
    border-radius: 6px;
    background: #fff;
  }
  .details {
    position: absolute;
    left: 400px;
    right: 30px;
    top: 92px;
    text-align: center;
    font-size: 19px;
    line-height: 1.65;
  }
  .appointment {
    position: absolute;
    left: 420px;
    right: 34px;
    bottom: 40px;
    display: flex;
    align-items: flex-end;
    gap: 12px;
    font-size: 17px;
  }
  .appointment__line {
    flex: 1;
    border-bottom: 1.5px solid var(--line);
    height: 1px;
    margin-bottom: 4px;
  }
</style>
</head>
<body>
  <section class="card card--front">
    <div class="card__panel"></div>
    <div class="decor-mark" role="img" aria-label="Faint large line illustration of a groomed dog with a bow"></div>
    <div class="brand"><span class="brand__dot"></span>Luna Brisk</div>
  </section>

  <section class="card card--back">
    <div class="card__panel"></div>
    <div class="brand"><span class="brand__dot"></span>Luna Brisk</div>
    <div class="badge" role="img" aria-label="Insurance stamp"></div>
    <div class="details">
      <p>Professional grooming services</p>
      <p>1 705 318 6052</p>
      <p>lunabrisk@mailvale.net</p>
      <p>TWF certified/member</p>
      <p>Pet first aid certified</p>
    </div>
    <div class="appointment">
      <span>Next appointment</span>
      <span class="appointment__line"></span>
    </div>
  </section>
</body>
</html>
```